Remodeling brochure

We need an informative homeowner friendly brochure detailing our company and things we do. We are looking for an initial setup and ideas (# of pages, etc) and then we will send more content. We are uploading our logo design. We are a high end remodeling company specializing in kitchen & bath remodels. We sell ourselves on customer communication and attention to detail in our designs and remodels.

Target Market(s)

Residential homeowners

Contact Information for Business Card

Modern and attention grabbing

Requirements
Must have
• Name- Hearth & Tile Works<br/>Address- 718 NW Larkfield Drive Suite #207<br/> Ankeny, Iowa 50099<br/>Phone- 515-555-0184<br/>email-htworksiowa@example-mail.com

```html
<!DOCTYPE html>
<html lang="en">
<head>
<meta charset="utf-8">
<title>Hearth &amp; Tile Works — Remodeling Brochure</title>
<link href="https://fonts.googleapis.com/css2?family=Montserrat:wght@400;600;700&family=Open+Sans:wght@400;600;700&family=Lato:wght@400;700&display=swap" rel="stylesheet">
<style>
:root{
  --bg:#e4e7e8;
  --paper:#f7f7f7;
  --charcoal:#2a2a2a;
  --charcoal-deep:#1c1c1c;
  --charcoal-soft:#3c3c3c;
  --blue:#2f6fe8;
  --blue-light:#4aa3f0;
  --ink:#222;
  --muted:#555;
  --white:#fff;
}
*{box-sizing:border-box;margin:0;padding:0}
html,body{width:874px;height:1200px;overflow:hidden;background:var(--bg)}
body{position:relative;font-family:"Open Sans",sans-serif;color:var(--ink)}
.spread{position:absolute;left:20px;width:834px;height:560px;display:flex;box-shadow:0 6px 18px rgba(0,0,0,.18)}
.spread--covers{top:20px}
.spread--inside{top:620px}
.page{position:relative;width:417px;height:560px;overflow:hidden;background:var(--paper)}
.photo{position:absolute}
.brand-name{font-family:"Montserrat",sans-serif;font-weight:600;color:var(--blue-light);letter-spacing:.5px;white-space:nowrap}

/* back cover */
.back-panel{position:absolute;left:40px;top:40px;width:337px;height:400px;background:linear-gradient(180deg,var(--charcoal-soft),var(--charcoal-deep))}
.back-panel .brand-name{position:absolute;left:22px;top:345px;font-size:20px}
.back-contact{position:absolute;left:0;right:0;top:458px;text-align:center;font-family:"Lato",sans-serif;color:var(--ink)}
.back-contact .address{font-size:12px;line-height:16px}
.back-contact .phone{font-size:24px;font-weight:700;margin-top:8px}
.back-contact .email{font-size:12px}

/* front cover */
.page--front{background:linear-gradient(160deg,#3a3a3a,var(--charcoal-deep) 60%)}
.page--front .brand-name{position:absolute;left:28px;top:30px;font-size:22px}
.accent-line{position:absolute;background:var(--blue)}
.contact-band{position:absolute;left:0;right:0;top:420px;height:36px;background:linear-gradient(90deg,#1d4fc4,var(--blue) 60%,var(--blue-light));color:var(--white);font-family:"Open Sans",sans-serif;font-weight:700;font-size:13px;display:flex;align-items:center;justify-content:flex-end;padding-right:22px}

/* inside left */
.motto{position:absolute;left:40px;top:66px;font-family:"Montserrat",sans-serif;color:var(--blue);line-height:1}
.motto .big{font-size:25px;letter-spacing:2px;display:block}
.motto .small{font-size:15px;letter-spacing:1.5px;display:block;margin:2px 0 3px}
.section-title{position:absolute;left:40px;top:196px;font-family:"Montserrat",sans-serif;font-weight:700}
.section-title h2{font-size:14px;letter-spacing:.5px}
.section-title h3{font-size:10px;margin-top:2px}
.rule{position:absolute;left:40px;top:232px;width:210px;height:1px;background:var(--ink)}
.body-copy{position:absolute;left:40px;top:245px;width:320px;font-size:7.5px;line-height:11px;color:var(--muted)}
.body-copy p+p{margin-top:6px}

/* inside right */
.offers-title{position:absolute;left:200px;top:90px;font-family:"Montserrat",sans-serif;font-size:22px;letter-spacing:2px;color:var(--blue)}
.offer-list{position:absolute;left:200px;top:138px;width:200px;list-style:none}
.offer-list li{position:relative;padding-left:26px;margin-bottom:16px}
.offer-list li::before{content:"";position:absolute;left:0;top:2px;width:16px;height:16px;background:linear-gradient(135deg,var(--blue-light),var(--blue))}
.offer-list strong{display:block;font-size:8.5px;font-weight:700}
.offer-list span{display:block;font-size:6.5px;line-height:9px;color:var(--muted)}
.overview{position:absolute;left:26px;top:405px;width:380px;color:var(--white)}
.overview-label{font-family:"Montserrat",sans-serif;font-size:8px;letter-spacing:1px;margin-bottom:6px}
.overview-box{width:205px;background:linear-gradient(90deg,#2458d6,var(--blue));padding:8px 10px}
.overview-box div{font-size:8.5px;font-weight:700;border-bottom:1px solid rgba(255,255,255,.6);padding:3px 0}
.overview-copy{width:205px;margin-top:10px;font-size:6.8px;line-height:9.5px;color:#cfcfcf}
.overview-side{position:absolute;left:225px;top:30px;width:155px}
.overview-side h4{font-family:"Montserrat",sans-serif;font-weight:400;font-size:13px;letter-spacing:1.5px;text-align:right;margin-bottom:6px}
.overview-side p{font-size:6.8px;line-height:9.5px;color:#cfcfcf;padding-bottom:3px;margin-bottom:3px;border-bottom:1px solid #555}
</style>
</head>
<body>

<section class="spread spread--covers">
  <article class="page page--back">
    <div class="back-panel">
      <div class="photo" style="left:18px;top:18px;width:301px;height:150px;background:linear-gradient(160deg,#efe6df,#d9c49a 70%,#c9a764)" role="img" aria-label="Photo of a white kitchen with island and wood floor"></div>
      <div class="photo" style="left:18px;top:178px;width:301px;height:150px;background:linear-gradient(135deg,#8a5a32,#c9a06a 45%,#b7b4ae)" role="img" aria-label="Photo of a bathroom vanity with vessel sink and round mirror"></div>
      <div class="brand-name">Hearth &amp; Tile Works</div>
    </div>
    <div class="back-contact">
      <p class="address">718 NW Larkfield Drive Suite #207<br>Ankeny, Iowa 50099</p>
      <p class="phone">515-555-0184</p>
      <p class="email">email-htworksiowa@example-mail.com</p>
    </div>
  </article>

  <article class="page page--front">
    <div class="brand-name">Hearth &amp; Tile Works</div>
    <div class="photo" style="left:24px;top:80px;width:200px;height:160px;background:linear-gradient(160deg,#f2f2f0,#d8d4cc 60%,#8a7360)" role="img" aria-label="Photo of a bright white kitchen with pendant lights and bar stools"></div>
    <div class="photo" style="left:240px;top:80px;width:156px;height:110px;background:linear-gradient(135deg,#9fb0c8,#6e7f9a)" role="img" aria-label="Photo of a blue mosaic tile backsplash with faucet"></div>
    <div class="photo" style="left:24px;top:256px;width:170px;height:126px;background:linear-gradient(160deg,#f4f4f4,#c9c9c9)" role="img" aria-label="Photo of a white bathroom vanity with lights and mirrors"></div>
    <div class="photo" style="left:208px;top:206px;width:188px;height:176px;background:linear-gradient(145deg,#d9c2a0,#a88a66 60%,#6e5a44)" role="img" aria-label="Photo of a tiled bathroom with shower and toilet"></div>
    <div class="accent-line" style="left:232px;top:70px;width:2px;height:120px"></div>
    <div class="accent-line" style="left:30px;top:247px;width:170px;height:3px"></div>
    <div class="accent-line" style="left:200px;top:300px;width:2px;height:100px"></div>
    <div class="contact-band">515-555-0184 | email-htworksiowa@example-mail.com</div>
  </article>
</section>

<section class="spread spread--inside">
  <article class="page page--inside-left">
    <svg width="417" height="560" style="position:absolute;left:0;top:0" aria-hidden="true">
      <path d="M0 10 Q210 -4 417 18 L417 24 Q210 2 0 16 Z" fill="#2f6fe8"/>
      <path d="M0 440 Q230 390 417 410 L417 560 L0 560 Z" fill="#242424"/>
    </svg>
    <div class="motto"><span class="big">DREAMS</span><span class="small">DON'T WORK</span><span class="big">UNLESS</span><span class="big">YOU DO !!</span></div>
    <svg width="70" height="70" style="position:absolute;left:200px;top:72px" aria-hidden="true">
      <polygon points="18,2 52,2 69,35 52,68 18,68 1,35" fill="#2f6fe8"/>
    </svg>
    <div class="photo" style="left:258px;top:60px;width:80px;height:60px;background:linear-gradient(135deg,#c7b2a4,#e9e2dc)" role="img" aria-label="Photo of a technician installing a water heater"></div>
    <div class="photo" style="left:232px;top:126px;width:106px;height:54px;background:linear-gradient(135deg,#dfe3e3,#b9c2c0)" role="img" aria-label="Photo of a hand adjusting a shower valve"></div>
    <div style="position:absolute;left:345px;top:60px;width:72px;height:60px;background:#4a5362"></div>
    <div class="photo" style="left:345px;top:126px;width:72px;height:54px;background:linear-gradient(150deg,#8b7255,#4a3b2e)" role="img" aria-label="Photo of a dark wood kitchen cabinetry"></div>
    <div class="section-title"><h2>BRAND POSITIONING</h2><h3>BRAND POSITIONING</h3></div>
    <div class="rule"></div>
    <div class="body-copy">
      <p>Lorem ipsum dolor sit amet, consectetuer adipiscing elit, sed diam nonummy nibh euismod tincidunt ut laoreet dolore magna aliquam erat volutpat. Ut wisi enim ad minim veniam, quis nostrud exerci tation ullamcorper suscipit lobortis nisl ut aliquip ex ea commodo consequat.</p>
      <p>Duis autem vel eum iriure dolor in hendrerit in vulputate velit esse molestie consequat, vel illum dolore eu feugiat nulla facilisis at vero eros et accumsan et iusto odio dignissim qui blandit praesent luptatum zzril delenit augue duis dolore te feugait nulla facilisi.</p>
      <p>Lorem ipsum dolor sit amet, cons ectetuer adipiscing elit, sed diam nonummy nibh euismod tincidunt ut laoreet dolore magna aliquam erat volutpat. Ut wisi enim ad minim veniam, quis nostrud exerci tation ullamcorper suscipit lobortis nisl ut aliquip ex ea commodo consequat.</p>
    </div>
    <svg width="417" height="560" style="position:absolute;left:0;top:0" aria-hidden="true">
      <polygon points="0,462 70,432 0,492" fill="#2f6fe8"/>
    </svg>
    <div class="photo" style="left:0;top:477px;width:190px;height:83px;background:linear-gradient(160deg,#e9e4da,#b9ad98 55%,#5b5245)" role="img" aria-label="Photo of a polished granite countertop by a window"></div>
  </article>

  <article class="page page--inside-right">
    <svg width="417" height="560" style="position:absolute;left:0;top:0" aria-hidden="true">
      <path d="M0 18 Q210 2 417 30 L417 36 Q210 8 0 24 Z" fill="#4aa3f0"/>
      <path d="M0 380 Q200 360 417 395 L417 560 L0 560 Z" fill="#242424"/>
    </svg>
    <div class="photo" style="left:0;top:60px;width:180px;height:180px;background:linear-gradient(150deg,#c8b89c,#6e5a44 55%,#3b3129)" role="img" aria-label="Collage of photos of remodeled kitchens with dark cabinetry"></div>
    <h2 class="offers-title">OUR OFFERS</h2>
    <ul class="offer-list">
      <li><strong>Lorem ipsum dolor sit amet, consectetuer</strong><span>Diam nonummy nibh euismod tincidunt ut laoreet dolore magna.</span></li>
      <li><strong>Lorem ipsum dolor sit amet, consectetuer</strong><span>Diam nonummy nibh euismod tincidunt ut laoreet dolore magna.</span></li>
      <li><strong>Lorem ipsum dolor sit amet, consectetuer</strong><span>Diam nonummy nibh euismod tincidunt ut laoreet dolore magna.</span></li>
    </ul>
    <div class="overview">
      <p class="overview-label">OVER VIEW</p>
      <div class="overview-box">
        <div>Project Name :</div>
        <div>Client :</div>
        <div>Category :</div>
      </div>
      <p class="overview-copy">Lorem ipsum dolor sit amet, consectetuer adipiscing elit, sed diam nonummy nibh euismod tincidunt ut laoreet dolore magna aliquam erat volutpat. Ut wisi enim ad minim veniam, quis nostrud exerci tation ullamcorper suscipit lobortis nisl ut aliquip ex ea commodo consequat.</p>
      <div class="overview-side">
        <h4>OUR OFFERS</h4>
        <p>Lorem ipsum dolor sit amet, consectetuer adipiscing elit, sed diam nonummy nibh euismod</p>
        <p>Lorem ipsum dolor sit amet, consectetuer adipiscing elit, sed diam nonummy nibh euismod</p>
        <p>Lorem ipsum dolor sit amet, consectetuer adipiscing elit, sed diam nonummy nibh euismod</p>
      </div>
    </div>
  </article>
</section>

</body>
</html>
```